Brightmill Data Works

Our company is about IT hardwares and IT solutions. IT hardware such as PC, RAMS, storage and servers. IT solutions such as project management, BA. We are also selling new technology too.

Target Market(s)

Consumer, Small to Medium Business, Corporate

Requirements
Must have
• The business card must have the following:
• Name:
• Title:
• Contact Number:
• Email address:
• Website:
• Color: Must match the logo color upgrade

```html
<!DOCTYPE html>
<html lang="en">
<head>
<meta charset="utf-8">
<title>Brightmill Data Works – Business Card</title>
<link href="https://fonts.googleapis.com/css2?family=Oswald:wght@500;600&family=Lato:wght@400&display=swap" rel="stylesheet">
<style>
  :root {
    --stage: #141414;
    --card: #262626;
    --card-edge: #2e2e2e;
    --amber: #e39a2c;
    --white: #f2f2f2;
  }
  * { margin: 0; padding: 0; box-sizing: border-box; }
  html, body { width: 1200px; height: 912px; overflow: hidden; background: var(--stage); }
  .canvas { position: relative; width: 1200px; height: 912px; }

  .card {
    position: absolute;
    width: 580px; height: 332px;
    background: linear-gradient(160deg, var(--card-edge), var(--card));
    box-shadow: 0 18px 40px rgba(0,0,0,.55);
  }
  .card--front { left: 90px; top: 110px; }
  .card--back  { left: 530px; top: 470px; }

  /* Front */
  .brand {
    position: absolute; inset: 0;
    display: flex; flex-direction: column; align-items: center; justify-content: center; gap: 14px;
  }
  .brand__mark { width: 22px; height: 22px; background: var(--amber); }
  .brand__name {
    font-family: "Oswald", sans-serif; font-weight: 600;
    font-size: 40px; letter-spacing: 1px; color: var(--white);
    text-transform: uppercase;
  }

  /* Back */
  .person {
    position: absolute; right: 318px; top: 128px; text-align: right;
  }
  .person__name {
    font-family: "Oswald", sans-serif; font-weight: 500;
    font-size: 40px; line-height: 1; color: var(--amber); text-transform: uppercase;
  }
  .person__title {
    font-family: "Lato", sans-serif; font-size: 17px; color: var(--white); margin-top: 6px;
  }
  .divider {
    position: absolute; left: 282px; top: 80px; width: 1.5px; height: 170px; background: var(--amber);
  }
  .contact {
    position: absolute; left: 304px; top: 86px;
    font-family: "Lato", sans-serif; font-size: 15px; line-height: 22px; color: var(--white);
    list-style: none;
  }
  .contact__address { margin-bottom: 8px; }
  .contact__row { display: flex; align-items: center; gap: 10px; }
  .contact__icon { width: 14px; height: 14px; flex: none; fill: var(--amber); }
</style>
</head>
<body>
<main class="canvas">

  <section class="card card--front" aria-label="Card front">
    <div class="brand">
      <span class="brand__mark"></span>
      <span class="brand__name">Brightmill Data Works</span>
    </div>
  </section>

  <section class="card card--back" aria-label="Card back">
    <div class="person">
      <p class="person__name">Daniel Hartwell</p>
      <p class="person__title">Manager</p>
    </div>
    <span class="divider"></span>
    <ul class="contact">
      <li class="contact__address">418 Cedar Row<br>Houston, TX 77041</li>
      <li class="contact__row">
        <svg class="contact__icon" viewBox="0 0 16 16"><path d="M3 1l3 3-2 2c1 2 3 4 5 5l2-2 3 3-2 3C7 15 1 9 1 3z"/></svg>
        512 555 0142
      </li>
      <li class="contact__row">
        <svg class="contact__icon" viewBox="0 0 16 16"><rect x="4" y="1" width="8" height="4"/><rect x="1" y="6" width="14" height="6" rx="1"/><rect x="4" y="10" width="8" height="5"/></svg>
        512 555 0143
      </li>
      <li class="contact__row">
        <svg class="contact__icon" viewBox="0 0 16 16"><path d="M1 3h14v10H1z M1 3l7 6 7-6" fill="var(--amber)" stroke="var(--card)" stroke-width="1"/></svg>
        info@brightmilldata.com
      </li>
      <li class="contact__row">
        <svg class="contact__icon" viewBox="0 0 16 16"><circle cx="8" cy="8" r="7"/><path d="M1 8h14M8 1c-3 4-3 10 0 14M8 1c3 4 3 10 0 14" stroke="var(--card)" stroke-width="1" fill="none"/></svg>
        www.brightmilldata.com
      </li>
    </ul>
  </section>

</main>
</body>
</html>
```